Create a memorable Web Design for real estate branding

we are a Minnepolis brokerage and boutique housing specialist with over 27 years of experience in the Global furnished housing industry, servicing the Greater Los Angeles area. Specializing in “warm environments” we offer a customized approach to satisfying our guests and client’s needs by offering a wide array of options in highly desirable areas. Additionally, Lantern Dwelling Partners offers assistance and expertise to home buyers, sellers and investors.

Industry/Entity Type

Real Estate

Number of Pages Required

1 page

Font styles to use
Serif
Sans Serif
Decorative

```html
<!DOCTYPE html>
<html lang="en">
<head>
<meta charset="utf-8">
<title>Lantern Dwelling Partners — Real Estate</title>
<link href="https://fonts.googleapis.com/css2?family=Raleway:wght@400;500;600&family=Open+Sans:ital,wght@0,400;0,600;1,400&display=swap" rel="stylesheet">
<style>
:root{
  --teal:#179a74;
  --teal-dark:#0f7d5e;
  --teal-light:#22ab83;
  --lime:#84c225;
  --grey-bg:#eeeeee;
  --footer-bg:#e4e4e4;
  --ink:#333333;
  --muted:#777777;
  --white:#ffffff;
}
*{margin:0;padding:0;box-sizing:border-box}
html,body{width:1200px;height:2171px;overflow:hidden;background:var(--white)}
body{position:relative;font-family:"Open Sans",Arial,sans-serif;color:var(--ink)}
.abs{position:absolute}

/* header */
.site-header{left:0;top:0;width:1200px;height:117px;background:var(--white)}
.brand{left:142px;top:40px;display:flex;align-items:center;gap:12px}
.brand-mark{width:18px;height:18px;background:var(--teal)}
.brand-name{font-family:"Raleway",sans-serif;font-weight:600;font-size:28px;color:var(--teal);letter-spacing:.5px}
.phone{left:903px;top:70px;display:flex;align-items:center;gap:6px;font-family:"Raleway",sans-serif;font-size:19px;color:var(--ink)}

/* nav */
.main-nav{left:0;top:117px;width:1200px;height:52px;background:linear-gradient(#22a982,#128a67)}
.main-nav ul{list-style:none;position:absolute;left:139px;top:0;height:52px;display:flex}
.main-nav li{height:52px;display:flex;align-items:center;padding:0 41px;font-family:"Raleway",sans-serif;font-weight:500;font-size:15px;color:var(--white);border-right:1px solid rgba(255,255,255,.22)}
.main-nav li:last-child{border-right:none}
.main-nav li.active{background:var(--teal-dark);padding:0 22px 0 21px}

/* hero */
.hero{left:0;top:169px;width:1200px;height:500px}
.hero-title{left:155px;top:340px;font-family:"Raleway",sans-serif;color:var(--white);font-weight:600;line-height:1.05;text-shadow:0 1px 4px rgba(0,0,0,.4)}
.hero-title .small{display:block;font-size:29px}
.hero-title .big{display:block;font-size:43px;letter-spacing:.5px}
.dots{left:563px;top:585px;display:flex;gap:5px}
.dots span{width:16px;height:16px;border-radius:50%;background:var(--white);border:2px solid rgba(0,0,0,.15)}
.dots span.on{background:#f3c74a}

/* cards */
.card{top:676px;width:290px;height:287px;border:1px solid #d9d9d9;background:var(--white)}
.card-photo{width:288px;height:153px}
.card h3{position:absolute;left:24px;top:168px;font-family:"Raleway",sans-serif;font-weight:400;font-size:20px;color:var(--ink)}
.card p{position:absolute;left:24px;top:200px;width:250px;font-size:11.5px;line-height:19px;color:var(--muted)}
.card .btn{position:absolute;left:-1px;bottom:-1px;width:101px;height:29px;background:var(--teal);color:var(--white);font-size:11px;font-weight:600;display:flex;align-items:center;justify-content:center}

/* welcome */
.welcome{left:0;top:1025px;width:1200px;height:295px;background:var(--grey-bg);text-align:center}
.chevron{left:567px;top:999px}
.welcome h2{position:absolute;left:0;top:80px;width:1200px;font-family:"Raleway",sans-serif;font-weight:400;font-size:26px;color:#444}
.welcome p{position:absolute;left:140px;top:126px;width:920px;font-size:14px;line-height:31px;color:var(--muted)}

/* features */
.feature{top:1377px;width:449px;height:249px;overflow:hidden}
.feature-text{position:absolute;color:var(--white);text-align:center;width:190px}
.feature-text h4{font-family:"Raleway",sans-serif;font-weight:400;font-size:20px;margin-top:6px}
.feature-text p{font-size:11px;line-height:16px;opacity:.8;margin-top:6px}
.feature-text .outline-btn{display:inline-block;margin-top:10px;width:100px;height:32px;line-height:30px;border:2px solid var(--white);font-size:12px}

/* testimonials */
.testimonials{left:0;top:1678px;width:1200px;height:356px;background:var(--lime)}
.testimonials h2{position:absolute;left:601px;top:87px;font-family:"Raleway",sans-serif;font-weight:400;font-size:23px;color:var(--white)}
.quote{left:601px;top:131px;width:430px;font-style:italic;font-size:16px;line-height:27px;color:#eef7dc}
.author{left:606px;top:250px;font-size:15px;font-weight:600;color:var(--white)}

/* footer */
.site-footer{left:0;top:2034px;width:1200px;height:137px;background:var(--footer-bg)}
.footer-nav{left:142px;top:42px;font-family:"Raleway",sans-serif;font-size:14px;color:#333;word-spacing:2px}
.copyright{left:142px;top:76px;font-size:12px;color:#555}
.social{left:923px;top:36px;display:flex;gap:4px}
.social span{width:30px;height:30px;border-radius:50%;border:1.5px solid #555}
</style>
</head>
<body>

<header class="site-header abs">
  <div class="brand abs"><span class="brand-mark"></span><span class="brand-name">Lantern Dwelling Partners</span></div>
  <div class="phone abs">
    <svg width="26" height="26" viewBox="0 0 26 26"><circle cx="13" cy="13" r="13" fill="#84c225"/><path d="M9 7c1 0 2 3 1.5 3.5L9.5 11.5c.8 2 2.5 3.8 4.7 4.8l1-1c.6-.5 3.5.6 3.5 1.5 0 1.2-1.4 2.2-2.5 2.2C11 19 7 15 7 9.6 7 8.4 8 7 9 7z" fill="#fff"/></svg>
    555-014-2738
  </div>
</header>

<nav class="main-nav abs">
  <ul>
    <li class="active">HOME</li><li>ABOUT US</li><li>SERVICES</li><li>PROPERTY</li><li>TESTIMONIAL</li><li>BROKERAGE</li><li>CONTACT</li>
  </ul>
</nav>

<section class="hero abs">
  <svg width="1200" height="500" viewBox="0 0 1200 500" role="img" aria-label="Photo of a lit modern two-storey house with patio at dusk, framed by autumn trees">
    <defs>
      <linearGradient id="heroSky" x1="0" y1="0" x2="0" y2="1">
        <stop offset="0" stop-color="#3d4a6e"/><stop offset=".55" stop-color="#5a5f6e"/><stop offset="1" stop-color="#3c4a2e"/>
      </linearGradient>
      <radialGradient id="heroGlow" cx=".6" cy=".6" r=".4"><stop offset="0" stop-color="#c89a55" stop-opacity=".55"/><stop offset="1" stop-color="#c89a55" stop-opacity="0"/></radialGradient>
    </defs>
    <rect width="1200" height="500" fill="url(#heroSky)"/>
    <rect width="1200" height="500" fill="url(#heroGlow)"/>
    <path d="M0 500 L0 497 Q600 370 1200 430 L1200 500 Z" fill="#ffffff"/>
  </svg>
</section>
<h1 class="hero-title abs"><span class="small">SPECIALIZING IN</span><span class="big">WARM ENVIRONMENTS</span></h1>
<div class="dots abs"><span class="on"></span><span></span><span></span><span></span></div>

<article class="card abs" style="left:143px">
  <svg class="card-photo" viewBox="0 0 288 153" role="img" aria-label="Photo of an agent handing house keys to a client"><rect width="288" height="153" fill="#e4ddd6"/></svg>
  <h3>Why Choose Us</h3>
  <p>Praesent elementum elit at tellus Curabitur metus ipsum luctus eu malesuada</p>
  <span class="btn">READ MORE</span>
</article>
<article class="card abs" style="left:453px">
  <svg class="card-photo" viewBox="0 0 288 153" role="img" aria-label="Photo of a housing specialist meeting with a couple"><rect width="288" height="153" fill="#ddd9d6"/></svg>
  <h3>Housing Specialist</h3>
  <p>Praesent elementum elit at tellus Curabitur metus ipsum luctus eu malesua</p>
  <span class="btn">READ MORE</span>
</article>
<article class="card abs" style="left:763px">
  <svg class="card-photo" viewBox="0 0 288 153" role="img" aria-label="Photo of a suburban house with a front lawn">
    <defs><linearGradient id="propSky" x1="0" y1="0" x2="0" y2="1"><stop offset="0" stop-color="#7b93c4"/><stop offset=".6" stop-color="#b7b6b0"/><stop offset="1" stop-color="#4f7a34"/></linearGradient></defs>
    <rect width="288" height="153" fill="url(#propSky)"/>
  </svg>
  <h3>Our Properties</h3>
  <p>Praesent elementum elit at tellus Curabitur metus ipsum luctus eu malesua</p>
  <span class="btn">READ MORE</span>
</article>

<section class="welcome abs">
  <h2>WELCOME TO OUR WEBSITE MAINPAGE</h2>
  <p>Cras a ante vitae enim iaculis aliquam Mauris nunc quam venenatis nec euismod sit amet egestas placerat est Pellentesque habitant morbi tristique senectus et netus et malesuada fames ac turpis egestas Cras id elit Integer quis urna Ut ante enim dapibus malesuada fringilla eu condimentum quis tellus Aenean porttitor eros vel dolo</p>
</section>
<svg class="chevron abs" width="66" height="50" viewBox="0 0 66 50">
  <path d="M0 17 A33 33 0 0 0 66 17 L66 0 L0 0 Z" fill="#ffffff"/>
  <circle cx="33" cy="17" r="33" fill="#ffffff"/>
  <path d="M23 14 L33 23 L43 14" fill="none" stroke="#84c225" stroke-width="3"/>
</svg>

<div class="feature abs" style="left:138px">
  <svg class="abs" width="449" height="249" viewBox="0 0 449 249" role="img" aria-label="Photo of a boutique bedroom with orange curtains">
    <rect width="449" height="249" fill="#6b5a4c"/>
    <rect width="180" height="249" fill="#8a4f33" opacity=".55"/>
    <circle cx="352" cy="122" r="135" fill="#84c225" opacity=".95"/>
  </svg>
  <div class="feature-text" style="left:257px;top:36px">
    <svg width="40" height="50" viewBox="0 0 40 50"><rect x="4" y="4" width="32" height="42" fill="none" stroke="#fff" stroke-width="2"/><rect x="10" y="12" width="20" height="26" fill="none" stroke="#fff" stroke-width="2"/><line x1="20" y1="12" x2="20" y2="38" stroke="#fff" stroke-width="2"/></svg>
    <h4>Boutique Housing</h4>
    <p>Cras a ante vitae enim iaculis aliquam Mauris nunc</p>
    <span class="outline-btn">Read More</span>
  </div>
</div>
<div class="feature abs" style="left:609px">
  <svg class="abs" width="449" height="249" viewBox="0 0 449 249" role="img" aria-label="Photo of a couple reviewing paperwork on a sofa">
    <rect width="449" height="249" fill="#4a4a4a"/>
    <rect x="200" width="249" height="249" fill="#6e6660" opacity=".6"/>
    <circle cx="110" cy="122" r="140" fill="#179a74" opacity=".95"/>
  </svg>
  <div class="feature-text" style="left:15px;top:46px">
    <svg width="64" height="40" viewBox="0 0 64 40"><path d="M4 14 L16 6 L28 10 L36 6 L48 6 L60 14 L50 26 L38 34 L26 30 L14 24 Z" fill="#fff"/></svg>
    <h4>Brokerage Service</h4>
    <p>Cras a ante vitae enim iaculis aliquam Mauris nunc</p>
    <span class="outline-btn">Read More</span>
  </div>
</div>

<section class="testimonials abs">
  <svg class="abs" width="600" height="356" viewBox="0 0 600 356" role="img" aria-label="Photo of a family relaxing together in a bright living room and kitchen">
    <path d="M0 0 L579 0 L499 356 L0 356 Z" fill="#cfc5b8"/>
    <path d="M146 150 L136 172 L146 194" fill="none" stroke="#fff" stroke-width="3"/>
  </svg>
  <svg class="abs" style="left:486px;top:121px" width="100" height="100" viewBox="0 0 100 100" role="img" aria-label="Portrait photo of the client giving the testimonial">
    <circle cx="50" cy="50" r="48" fill="#b9b2aa" stroke="#fff" stroke-width="4"/>
  </svg>
  <h2>TESTIMONIALS</h2>
  <p class="quote abs">“ Morbi diam mauris viverra in gravida eu mattis in ante Morbi eget arcu Morbi porta libero id ullamcorper nonummy nibh ligula pulvinar metus eget consectetuer augue nisi quis lacus Ut ac mi ”</p>
  <p class="author abs">By Author Name</p>
  <svg class="abs" style="left:1044px;top:150px" width="20" height="44" viewBox="0 0 20 44"><path d="M4 4 L16 22 L4 40" fill="none" stroke="#fff" stroke-width="3"/></svg>
</section>

<footer class="site-footer abs">
  <p class="footer-nav abs">HOME &nbsp;|&nbsp; ABOUT &nbsp;|&nbsp; SERVICES &nbsp;|&nbsp; PROPERTY &nbsp;|&nbsp; TESTIMONIAL &nbsp;|&nbsp; CONTACT</p>
  <p class="copyright abs">© 2016 Company Name &nbsp;All right reserved &nbsp;Term of Use</p>
  <div class="social abs"><span></span><span></span><span></span><span></span></div>
</footer>

</body>
</html>
```